Request for Business Card Design

Hi. My name is Marlene, I am looking for a new business card design for my company, Quarrow Signal Instruments, LLC. I really like the design you did for Tarsel Venture and was hoping you could do something similar using our full logo and our mark. I am also open to any raised texture design using our mark. I have attached our full logo, which would need to be somewhere on the card, as well as the mark in both outline and full form, as well as our brand colors / guide. The card does not have to be white, as long as our logo and mark appear. I actually like darker colored business cards more, but am open to all options. If you are interested in working with me, please let me know. We would also take the business card design into letterhead design if you can do that.

```html
<!DOCTYPE html>
<html lang="en">
<head>
<meta charset="utf-8">
<title>Quarrow Signal Instruments — Stationery</title>
<link href="https://fonts.googleapis.com/css2?family=Barlow:wght@600&family=Lato:wght@400;700&family=Montserrat:wght@400;600&family=Tangerine:wght@700&display=swap" rel="stylesheet">
<style>
  :root {
    --backdrop: #cdc6c6;
    --paper: #ffffff;
    --brand-blue: #0f9ac4;
    --brand-blue-deep: #0a93c2;
    --ink: #3a3a3c;
    --ink-soft: #444447;
    --arc-dark: #3d3b3d;
  }
  * { box-sizing: border-box; margin: 0; padding: 0; }
  html, body { width: 1200px; height: 900px; overflow: hidden; }
  body { background: var(--backdrop); position: relative; font-family: "Lato", sans-serif; color: var(--ink); }

  .sheet, .card { position: absolute; background: var(--paper); overflow: hidden; box-shadow: 0 6px 14px rgba(0,0,0,.28); }

  /* Brand lockup */
  .lockup { position: absolute; display: flex; align-items: center; gap: 8px; }
  .lockup-dot { border-radius: 50%; background: var(--brand-blue); flex: none; }
  .lockup-name { font-family: "Barlow", sans-serif; font-weight: 600; color: var(--ink); line-height: 1; }
  .lockup-name .primary { display: block; letter-spacing: .06em; }
  .lockup-name .secondary { display: block; letter-spacing: .04em; margin-top: 2px; }

  /* Letterhead */
  .letterhead { left: 238px; top: 112px; width: 464px; height: 657px; }
  .letterhead .lockup { left: 37px; top: 48px; }
  .letterhead .lockup-dot { width: 38px; height: 38px; }
  .letterhead .primary { font-size: 25px; }
  .letterhead .secondary { font-size: 8px; }

  .contact { position: absolute; font-family: "Montserrat", sans-serif; color: var(--ink); }
  .contact li { list-style: none; display: flex; align-items: center; gap: 5px; }
  .contact svg { flex: none; }
  .letterhead .contact { left: 314px; top: 34px; border-left: 1px solid var(--brand-blue); padding-left: 5px; font-size: 7.4px; line-height: 10.5px; }
  .letterhead .contact .address { margin-bottom: 4px; }
  .letterhead .contact li { margin-top: 1.5px; }

  .letter { position: absolute; left: 36px; top: 151px; width: 392px; font-size: 8.7px; line-height: 10.2px; color: var(--ink-soft); }
  .letter .date { margin-bottom: 12px; }
  .letter .recipient { margin-bottom: 10px; }
  .letter .salutation { font-weight: 700; font-size: 10.6px; margin: 8px 0 11px; color: var(--ink); }
  .letter .para { text-align: justify; margin-bottom: 10px; }
  .letter .closing { margin-top: 20px; }
  .letter .signature { font-family: "Tangerine", cursive; font-size: 26px; line-height: 30px; margin-top: 9px; color: var(--ink); }

  .sheet-wave, .card-wave { position: absolute; left: 0; bottom: 0; }

  /* Business card front */
  .card-front { left: 724px; top: 372px; width: 324px; height: 185px; }
  .card-front .lockup { left: 22px; top: 60px; gap: 7px; }
  .card-front .lockup-dot { width: 30px; height: 30px; }
  .card-front .primary { font-size: 19px; }
  .card-front .secondary { font-size: 6.2px; }
  .holder { position: absolute; left: 180px; top: 51px; border-left: 1px solid var(--brand-blue); padding-left: 7px; height: 66px; }
  .holder-name { font-family: "Montserrat", sans-serif; font-weight: 600; font-size: 9.6px; color: var(--ink); letter-spacing: .01em; }
  .holder-name .surname { color: var(--brand-blue); }
  .holder-role { font-family: "Montserrat", sans-serif; font-size: 8px; margin-top: 1px; }
  .card-front .contact { position: static; margin-top: 8px; font-size: 8px; line-height: 13px; }

  /* Business card back */
  .card-back { left: 723px; top: 579px; width: 326px; height: 189px; background: var(--brand-blue-deep); }
  .card-back .lockup { left: 62px; top: 67px; gap: 9px; }
  .card-back .lockup-dot { width: 46px; height: 46px; background: var(--paper); }
  .card-back .lockup-name { color: var(--paper); }
  .card-back .primary { font-size: 28px; }
  .card-back .secondary { font-size: 9px; }
</style>
</head>
<body>

<!-- Letterhead -->
<section class="sheet letterhead">
  <div class="lockup">
    <span class="lockup-dot"></span>
    <div class="lockup-name"><span class="primary">QUARROW</span><span class="secondary">SIGNAL INSTRUMENTS</span></div>
  </div>

  <ul class="contact">
    <li class="address">41-06 Fenwick Row 12<br>Alder Bay, NY 11492</li>
    <li><svg width="8" height="8" viewBox="0 0 10 10"><path d="M2 1l2 2-1 1.3c.7 1.3 1.4 2 2.7 2.7L7 6l2 2-1.3 1.3C4.5 9 1 5.5.7 2.3z" fill="var(--brand-blue)"/></svg>555-0184-2263</li>
    <li><svg width="8" height="8" viewBox="0 0 10 8"><rect x="0" y="0" width="10" height="8" fill="var(--brand-blue)"/><path d="M0 0l5 4 5-4" stroke="#fff" stroke-width="1" fill="none"/></svg>hello@quarrow-signal.com</li>
    <li><svg width="8" height="8" viewBox="0 0 10 10"><circle cx="5" cy="5" r="4.6" fill="var(--brand-blue)"/><path d="M.5 5h9M5 .5c-2.5 2.5-2.5 6.5 0 9M5 .5c2.5 2.5 2.5 6.5 0 9" stroke="#fff" stroke-width=".7" fill="none"/></svg>www.quarrow-signal.com</li>
  </ul>

  <div class="letter">
    <p class="date">Feb-03-2022</p>
    <p class="recipient">Mr, Ellis Varden<br>President</p>
    <p class="recipient">Brightfold Corporation<br>123 Street Name, Suite# 10<br>City, State, 120023</p>
    <p class="salutation">Dear Mr, Ellis</p>
    <p class="para">Lorem ipsum dolor sit amet, consectetur adipisicing elit, sed do eiusmod tempor incididunt ut labore et dolore magna aliqua. Ut enim ad minim veniam, quis nostrud exercitation ullamco laboris nisi ut aliquip ex ea commodo consequat. Duis aute irure dolor in reprehenderit in voluptate velit esse cillum dolore eu fugiat nulla pariatur.</p>
    <p class="para">Lorem ipsum dolor sit amet, consectetur adipisicing elit, sed do eiusmod tempor incididunt ut labore et dolore magna aliqua. Ut enim ad minim veniam, quis nostrud exercitation ullamco laboris nisi ut aliquip ex ea commodo consequat. Duis aute irure dolor in reprehenderit in voluptate velit esse cillum dolore eu fugiat nulla pariatur.</p>
    <p class="para">Lorem ipsum dolor sit amet, consectetur adipisicing elit, sed do eiusmod tempor incididunt ut labore et dolore magna aliqua. Ut enim ad minim veniam, quis nostrud exercitation ullamco laboris nisi ut aliquip ex ea commodo consequat.</p>
    <p class="para">Excepteur sint occaecat cupidatat non proident, sunt in culpa qui officia deserunt mollit anim id est laborum. re et dolore magnam aliquam quaerat voluptatem.</p>
    <p class="closing">Regards</p>
    <p class="signature">Owen Hartley</p>
  </div>

  <svg class="sheet-wave" width="464" height="90" viewBox="0 0 464 90">
    <path d="M0 3 Q232 92 464 0 V90 H0 Z" fill="var(--brand-blue-deep)"/>
    <path d="M18 5 Q232 80 437 6 Q232 68 18 5 Z" fill="var(--paper)"/>
    <path d="M18 5 Q232 70 437 6 Q232 58 18 5 Z" fill="var(--arc-dark)"/>
  </svg>
</section>

<!-- Business card, front -->
<section class="card card-front">
  <div class="lockup">
    <span class="lockup-dot"></span>
    <div class="lockup-name"><span class="primary">QUARROW</span><span class="secondary">SIGNAL INSTRUMENTS</span></div>
  </div>

  <div class="holder">
    <p class="holder-name">DARA <span class="surname">WHITLOCK</span></p>
    <p class="holder-role">Owner</p>
    <ul class="contact">
      <li><svg width="8" height="8" viewBox="0 0 10 10"><path d="M2 1l2 2-1 1.3c.7 1.3 1.4 2 2.7 2.7L7 6l2 2-1.3 1.3C4.5 9 1 5.5.7 2.3z" fill="var(--brand-blue)"/></svg>555.627.0419</li>
      <li><svg width="8" height="7" viewBox="0 0 10 8"><rect x="0" y="0" width="10" height="8" fill="var(--brand-blue)"/><path d="M0 0l5 4 5-4" stroke="#fff" stroke-width="1" fill="none"/></svg>info@quarrowsignal.com</li>
      <li><svg width="8" height="8" viewBox="0 0 10 10"><circle cx="5" cy="5" r="4.6" fill="var(--brand-blue)"/><path d="M.5 5h9M5 .5c-2.5 2.5-2.5 6.5 0 9M5 .5c2.5 2.5 2.5 6.5 0 9" stroke="#fff" stroke-width=".7" fill="none"/></svg>www.quarrowsignal.com</li>
    </ul>
  </div>

  <svg class="card-wave" width="324" height="53" viewBox="0 0 324 53">
    <path d="M0 0 Q162 60 324 0 V53 H0 Z" fill="var(--brand-blue-deep)"/>
    <path d="M18 3 Q162 52 300 4 Q162 44 18 3 Z" fill="var(--paper)"/>
    <path d="M18 3 Q162 45 300 4 Q162 37 18 3 Z" fill="var(--arc-dark)"/>
  </svg>
</section>

<!-- Business card, back -->
<section class="card card-back">
  <div class="lockup">
    <span class="lockup-dot"></span>
    <div class="lockup-name"><span class="primary">QUARROW</span><span class="secondary">SIGNAL INSTRUMENTS</span></div>
  </div>
</section>

</body>
</html>
```